Awesome photographers card for an awesome new business

Double sided business card Black background and silver logo in middle on one side. Details on otherside. please keep it simple

Industry/Entity Type

Photographer

Contact Information for Business Card

Gerald Fenwick
0452817360
GeraldFenwickPhotography47@mailbox.test
www.GeraldFenwickPhotography.test.au
Instagram _Gerald_fenwick

Requirements
Must have
• My logo in Silver
• please use instagram logo instead of "Instagram"

```html
<!DOCTYPE html>
<html lang="en">
<head>
<meta charset="utf-8">
<title>Gerald Fenwick Photography – Business Card</title>
<link rel="stylesheet" href="https://fonts.googleapis.com/css2?family=Open+Sans:wght@400;600&display=swap">
<style>
  :root {
    --backdrop: #6a4732;
    --card: #0b0b0b;
    --silver: #c8c8c8;
    --silver-soft: #a9a9a9;
    --text: #bdbdbd;
  }
  html, body {
    margin: 0;
    width: 1200px;
    height: 1000px;
    overflow: hidden;
    background: var(--backdrop);
    font-family: "Open Sans", Arial, sans-serif;
  }
  .card {
    position: absolute;
    left: 267px;
    width: 665px;
    height: 396px;
    background: var(--card);
    box-shadow: 0 6px 18px rgba(0,0,0,0.45);
    overflow: hidden;
  }
  .card--front { top: 75px; }
  .card--back { top: 534px; }

  .brand {
    position: absolute;
    display: flex;
    align-items: center;
    gap: 14px;
    color: var(--silver);
    font-weight: 400;
    letter-spacing: 0.18em;
    text-transform: uppercase;
    white-space: nowrap;
  }
  .brand__dot {
    width: 14px;
    height: 14px;
    border-radius: 50%;
    background: var(--silver);
    flex: none;
  }
  .card--front .brand {
    left: 50%;
    top: 50%;
    transform: translate(-50%, -50%);
    font-size: 22px;
  }
  .card--back .brand {
    right: 48px;
    top: 122px;
    font-size: 13px;
    gap: 10px;
  }
  .card--back .brand__dot { width: 10px; height: 10px; }

  .person {
    position: absolute;
    left: 33px;
    top: 192px;
  }
  .person__name {
    margin: 0;
    color: var(--text);
    font-size: 22px;
    font-weight: 400;
    line-height: 1.2;
    letter-spacing: 0.01em;
  }
  .person__role {
    margin: 2px 0 0;
    color: var(--text);
    font-size: 15px;
    line-height: 1.3;
  }
  .contacts {
    position: absolute;
    left: 33px;
    top: 260px;
    margin: 0;
    padding: 0;
    list-style: none;
  }
  .contacts__item {
    display: flex;
    align-items: center;
    gap: 8px;
    height: 22px;
    color: var(--text);
    font-size: 15px;
  }
  .contacts__icon {
    width: 12px;
    height: 12px;
    flex: none;
    fill: var(--silver-soft);
  }
  .contacts__square {
    width: 10px;
    height: 10px;
    margin: 0 1px;
    background: var(--silver-soft);
    flex: none;
  }
</style>
</head>
<body>
  <section class="card card--front" aria-label="Card front">
    <div class="brand"><span class="brand__dot"></span>Gerald Fenwick Photography</div>
  </section>

  <section class="card card--back" aria-label="Card back">
    <div class="brand"><span class="brand__dot"></span>Gerald Fenwick Photography</div>

    <div class="person">
      <h1 class="person__name">GERALD FENWICK</h1>
      <p class="person__role">Photographer</p>
    </div>

    <ul class="contacts">
      <li class="contacts__item">
        <svg class="contacts__icon" viewBox="0 0 12 12" aria-hidden="true"><path d="M2.5 0.8 L4.4 3.2 L3.4 4.5 C4 6 5.8 7.9 7.5 8.6 L8.8 7.6 L11.2 9.5 L10 11.2 C5.5 11 1 6.5 0.8 2 Z"/></svg>
        0452817360
      </li>
      <li class="contacts__item">
        <span class="contacts__square" aria-hidden="true"></span>
        Gerald_fenwick
      </li>
      <li class="contacts__item">
        <svg class="contacts__icon" viewBox="0 0 12 12" aria-hidden="true"><path d="M0.5 2.5 H11.5 V9.5 H0.5 Z M1.2 3.1 L6 6.6 L10.8 3.1 Z" fill-rule="evenodd"/></svg>
        GeraldFenwickPhotography47@mailbox.test
      </li>
      <li class="contacts__item">
        <svg class="contacts__icon" viewBox="0 0 12 12" aria-hidden="true"><circle cx="6" cy="6" r="5.2" fill="none" stroke="#a9a9a9" stroke-width="1.3"/><path d="M0.8 6 H11.2 M6 0.8 C3.5 3.5 3.5 8.5 6 11.2 M6 0.8 C8.5 3.5 8.5 8.5 6 11.2" fill="none" stroke="#a9a9a9" stroke-width="1"/></svg>
        www.GeraldFenwickPhotography.test.au
      </li>
    </ul>
  </section>
</body>
</html>
```